Business Card Design Project

We are a construction company in Orange County, CA. We need a two sided business card. We would like the back to be our logo with web URL. Front should included Name, title, address, phone, fax and email address.

our address is
627 West Dorrance Blvd, Suite 308
Larkmoor, CA 92718

Our logo files are attached.

Construction

```html
<!DOCTYPE html>
<html lang="en">
<head>
<meta charset="utf-8">
<title>Torvanex Business Card</title>
<link rel="stylesheet" href="https://fonts.googleapis.com/css2?family=Open+Sans:wght@400;700;800&display=swap">
<style>
  :root {
    --navy: #1b4a7c;
    --grey-bar: #b3b3b3;
    --text-grey: #555555;
    --url-grey: #6b6b6b;
    --card: #ffffff;
    --backdrop: #e9e9e9;
  }
  * { margin: 0; padding: 0; box-sizing: border-box; }
  html, body { width: 1200px; height: 444px; overflow: hidden; }
  body {
    background: var(--backdrop);
    font-family: "Open Sans", Arial, sans-serif;
    position: relative;
  }
  .card {
    position: absolute;
    top: 75px;
    width: 515px;
    height: 294px;
    background: var(--card);
    border-radius: 14px;
    overflow: hidden;
    box-shadow: 0 2px 6px rgba(0,0,0,0.15);
  }
  .card--front { left: 72px; }
  .card--back { left: 612px; }

  .wordmark {
    position: absolute;
    color: var(--navy);
    font-weight: 800;
    font-size: 40px;
    line-height: 1;
    letter-spacing: -0.5px;
    white-space: nowrap;
  }
  .card--front .wordmark { left: 47px; top: 110px; }
  .card--back .wordmark { left: 52px; top: 127px; }

  .stripe { position: absolute; top: 263px; height: 12px; }
  .stripe--grey { left: 0; width: 315px; background: var(--grey-bar); }
  .stripe--navy { left: 319px; right: 0; background: var(--navy); }

  .contact { position: absolute; left: 334px; top: 49px; color: var(--text-grey); white-space: nowrap; }
  .contact__name { color: var(--navy); font-weight: 700; font-size: 17px; line-height: 22px; }
  .contact__title { font-size: 13px; line-height: 18px; margin-bottom: 9px; }
  .contact__list { list-style: none; }
  .contact__item { display: flex; align-items: center; font-size: 13.5px; line-height: 17.5px; }
  .contact__icon { width: 10px; height: 10px; margin-right: 9px; fill: var(--text-grey); flex: none; }
  .contact__address { font-style: normal; font-size: 13.5px; line-height: 18px; margin-top: 17px; }

  .card__url {
    position: absolute;
    left: 318px;
    top: 143px;
    font-size: 12px;
    letter-spacing: 2.2px;
    color: var(--url-grey);
    white-space: nowrap;
  }
</style>
</head>
<body>
  <section class="card card--front">
    <div class="wordmark">TORVANEX</div>
    <div class="contact">
      <div class="contact__name">YOUR NAME</div>
      <div class="contact__title">Title</div>
      <ul class="contact__list">
        <li class="contact__item">
          <svg class="contact__icon" viewBox="0 0 10 10"><path d="M2 0.5 L3.6 2.6 L2.8 3.6 Q4 6 6.4 7.2 L7.4 6.4 L9.5 8 L8.3 9.5 Q1.5 8.5 0.5 1.7 Z"/></svg>
          714 555 0142
        </li>
        <li class="contact__item">
          <svg class="contact__icon" viewBox="0 0 10 10"><rect x="2.5" y="0.5" width="5" height="3"/><rect x="0.5" y="3.5" width="9" height="4" rx="1"/><rect x="2.5" y="7" width="5" height="2.5"/></svg>
          714 555 0187
        </li>
        <li class="contact__item">
          <svg class="contact__icon" viewBox="0 0 10 10"><rect x="0.5" y="2" width="9" height="6.5"/><path d="M0.5 2 L5 5.5 L9.5 2" fill="none" stroke="#fff" stroke-width="0.9"/></svg>
          info@torvanex-build.com
        </li>
        <li class="contact__item">
          <svg class="contact__icon" viewBox="0 0 10 10"><circle cx="5" cy="5" r="4.5"/><path d="M0.5 5 H9.5 M5 0.5 V9.5 M5 0.5 Q2 5 5 9.5 M5 0.5 Q8 5 5 9.5" fill="none" stroke="#fff" stroke-width="0.7"/></svg>
          www.torvanex-build.com
        </li>
      </ul>
      <address class="contact__address">
        627 West Dorrance Blvd<br>
        Suite 308<br>
        Larkmoor, CA 92718
      </address>
    </div>
    <div class="stripe stripe--grey"></div>
    <div class="stripe stripe--navy"></div>
  </section>

  <section class="card card--back">
    <div class="wordmark">TORVANEX</div>
    <div class="card__url">www.torvanex-build.com</div>
    <div class="stripe stripe--grey"></div>
    <div class="stripe stripe--navy"></div>
  </section>
</body>
</html>
```